Summer Sunglass offer

Need a poster design for a spring / summer campaign. We are an opticians with good footfall. The design needs to be eye catching and aimed at 40 year old plus. The offer is Up to 50% off sunglass offer, t&c apply. (I have attached our last year campaign)
Also need a 2 sided A5 leaflet design (see attached)
I've uploaded a copy of our logo

A5 leaflet should read:

Grab a bargain on two great looks this summer Upto 50% off sunglasses
Look great and stay safe in the sun this summer

We want you to look great, feel fantastic and most of all stay safe in the sun this summer. That’s why we’re offering you 50% off prescription sunglasses with every complete pair of glasses you buy this summer or 25% off for prescription sunglasses with no other purchase.
Find you new summer looks from our gorgeous collection of frames in store. It matters to us that you look great in your new glasses as much as how well you see through them, so we’ll be on hand to help you find frames that suit you best.
What new looks will you go for? Smart or sassy? Formal or Fun? Whatever you’re in the mood for, you’ll find it in our collections this summer.
Call in today to find your new looks, and remember to bring your prescription if you don’t need an eye test.

Target Market(s)

40 + year old

Industry/Entity Type

Optician

Colors

Designer to choose colors to be used in the design.

Requirements
Must have
• Images, preferably a male and Female image

```html
<!DOCTYPE html>
<html lang="en">
<head>
<meta charset="utf-8">
<title>Harwell Eyecare Centre – Summer Sunglasses Offer</title>
<link rel="stylesheet" href="https://fonts.googleapis.com/css2?family=Lato:wght@400;700;900&display=swap">
<style>
  :root {
    --brand-blue: #0b4ea2;
    --brand-blue-dark: #0a4596;
    --paper: #ffffff;
    --paper-tint: #f3f4f6;
    --ring-tint: rgba(255, 255, 255, 0.55);
    --name-blue: #1f4f9c;
    --divider: #b9bec6;
  }
  * { margin: 0; padding: 0; box-sizing: border-box; }
  html, body {
    width: 1200px;
    height: 1200px;
    overflow: hidden;
    background: var(--paper);
  }
  .poster {
    position: relative;
    width: 1200px;
    height: 1200px;
    overflow: hidden;
    background: var(--paper-tint);
    font-family: "Lato", Arial, sans-serif;
  }
  .top-band {
    position: absolute;
    left: 0; top: 0;
    width: 1200px;
    height: 650px;
    background: var(--brand-blue);
  }
  .frame-line {
    position: absolute;
    left: 40px; top: 35px;
    width: 1120px;
    height: 615px;
    border: 3px solid var(--paper);
    border-bottom: none;
  }
  .headline {
    position: absolute;
    left: 310px; top: 48px;
    display: flex;
    align-items: baseline;
    color: var(--paper);
    font-weight: 900;
    text-transform: uppercase;
    white-space: nowrap;
    line-height: 1;
  }
  .headline .small { font-size: 51px; }
  .headline .big { font-size: 114px; margin: 0 30px 0 28px; }
  .headline .pct { font-size: 62px; margin-right: 30px; }
  .portrait-art {
    position: absolute;
    left: 0; top: 0;
  }
  .brand {
    position: absolute;
    left: 0; top: 935px;
    width: 1200px;
    display: flex;
    justify-content: center;
    align-items: center;
    gap: 22px;
  }
  .brand-divider {
    width: 2px; height: 112px;
    background: var(--divider);
  }
  .brand-name {
    color: var(--name-blue);
    font-weight: 700;
    text-transform: uppercase;
    line-height: 1.1;
  }
  .brand-name .line-1 { display: block; font-size: 56px; letter-spacing: 4px; }
  .brand-name .line-2 { display: block; font-size: 27px; letter-spacing: 7px; }
  .contact-bar {
    position: absolute;
    left: 102px; top: 1060px;
    width: 996px; height: 102px;
    background: var(--brand-blue-dark);
    border-radius: 8px;
    color: var(--paper);
    font-size: 26px;
    font-weight: 700;
  }
  .contact-bar::before {
    content: "";
    position: absolute;
    left: 476px; top: -20px;
    border-left: 20px solid transparent;
    border-right: 20px solid transparent;
    border-bottom: 20px solid var(--brand-blue-dark);
  }
  .contact-item {
    position: absolute;
    display: flex;
    align-items: center;
    gap: 14px;
    white-space: nowrap;
  }
  .contact-item svg { width: 28px; height: 28px; flex: none; }
  .item-address { left: 24px; top: 12px; }
  .item-web { left: 24px; top: 56px; }
  .item-phone { left: 560px; top: 12px; }
  .item-email { left: 560px; top: 56px; }
</style>
</head>
<body>
<main class="poster">
  <div class="top-band"></div>
  <div class="frame-line"></div>

  <h1 class="headline">
    <span class="small">Up to</span><span class="big">50</span><span class="pct">%</span><span class="small">Sunglasses</span>
  </h1>

  <svg class="portrait-art" width="1200" height="1200" viewBox="0 0 1200 1200">
    <defs>
      <linearGradient id="portraitTones" x1="0" y1="0" x2="0" y2="1">
        <stop offset="0" stop-color="#2a2a2c"/>
        <stop offset="0.35" stop-color="#d9c48f"/>
        <stop offset="0.6" stop-color="#e6c9b6"/>
        <stop offset="1" stop-color="#1c1c1e"/>
      </linearGradient>
      <clipPath id="bandClip"><rect x="0" y="0" width="1200" height="650"/></clipPath>
    </defs>
    <circle class="halo-ring" cx="600" cy="588" r="425" fill="var(--ring-tint)" clip-path="url(#bandClip)"/>
    <circle class="portrait-mat" cx="600" cy="588" r="381" fill="var(--paper)"/>
    <circle class="portrait-edge" cx="600" cy="588" r="348" fill="var(--brand-blue)"/>
    <circle class="portrait-photo" cx="600" cy="588" r="343" fill="url(#portraitTones)"
            role="img" aria-label="Photo of a blonde woman in a black wide-brimmed hat and polka-dot top, lifting her dark sunglasses"/>
  </svg>

  <div class="brand">
    <span class="brand-divider"></span>
    <span class="brand-name"><span class="line-1">Harwell</span><span class="line-2">Eyecare Centre</span></span>
  </div>

  <section class="contact-bar">
    <div class="contact-item item-address">
      <svg viewBox="0 0 24 24"><rect x="1" y="1" width="22" height="22" rx="4" fill="#fff"/><path d="M12 4.5a5 5 0 0 0-5 5c0 3.8 5 9.5 5 9.5s5-5.7 5-9.5a5 5 0 0 0-5-5z" fill="#0a4596"/><circle cx="12" cy="9.5" r="2" fill="#fff"/></svg>
      <span>48 Market St, Aldbrook, AB4 2QT.</span>
    </div>
    <div class="contact-item item-web">
      <svg viewBox="0 0 24 24" fill="none" stroke="#fff" stroke-width="1.8"><circle cx="12" cy="12" r="9.5"/><ellipse cx="12" cy="12" rx="4.2" ry="9.5"/><path d="M2.5 12h19M4 7h16M4 17h16"/></svg>
      <span>www.harwelleyecare.co.uk</span>
    </div>
    <div class="contact-item item-phone">
      <svg viewBox="0 0 24 24"><rect x="1" y="1" width="22" height="22" rx="5" fill="none" stroke="#fff" stroke-width="2"/><path d="M5 10c0-3 14-3 14 0l-2 1.5-2.5-1.5v-1.5c-2-.6-3-.6-5 0V10L7 11.5z" fill="#fff"/><circle cx="12" cy="15" r="2.6" fill="none" stroke="#fff" stroke-width="1.8"/></svg>
      <span>01632960418</span>
    </div>
    <div class="contact-item item-email">
      <svg viewBox="0 0 24 24" fill="none" stroke="#fff" stroke-width="1.8"><rect x="2" y="5" width="20" height="14" rx="1"/><path d="M2 5l10 8 10-8M2 19l7.5-7M22 19l-7.5-7"/></svg>
      <span>info@harwelleyecare.co.uk</span>
    </div>
  </section>
</main>
</body>
</html>
```